Academic and Business book cover

I need a book cover for my academic and business book.
The focus is in international / global negotiation and influence (how to negotiate across cultures).
The book will be published on Zelvorn, both in Vaspet and printed edition. therefore I need something that works under Zelvorn guidelines.The final design should be elegant and still be able to stand out against the competition.
I would like to have orange+grey for the text colors on the cover, even if different options are welcome.
Title and my name are in the attached word doc.

Target Market(s)

graduates, Phds, from international business schools. Managers

Industry/Entity Type

Business

Font styles to use
Serif
Sans Serif

Colors

Designer to choose colors to be used in the design.

Requirements
Must have
• The title and my name should have elegant fonts.
Nice to have
• pictures of the world that don't have the "usual" Europe in the centre.

```html
<!DOCTYPE html>
<html lang="en">
<head>
<meta charset="utf-8">
<title>The 4Cs Approach – Cover Options</title>
<link rel="stylesheet" href="https://fonts.googleapis.com/css2?family=Inter:wght@400;500;700&display=swap">
<style>
  :root {
    --page-bg: #ffffff;
    --cover-charcoal: #2b2b2b;
    --cover-midnight: #1b1a24;
    --title-orange: #f5a93a;
    --subtitle-white: #f2f2f2;
    --tab-slate: #3d4a4e;
    --art-green: #6b9440;
    --art-blue: #3a6da0;
    --art-teal: #1f8fa8;
    --art-plum: #6a3f90;
    --art-rose: #a7607e;
  }
  html, body {
    margin: 0;
    width: 1200px;
    height: 1000px;
    overflow: hidden;
    background: var(--page-bg);
    font-family: "Inter", Helvetica, Arial, sans-serif;
  }
  .canvas { position: relative; width: 1200px; height: 1000px; }
  .cover {
    position: absolute;
    top: 165px;
    width: 478px;
    height: 708px;
    overflow: hidden;
    box-shadow: 4px 6px 10px rgba(0,0,0,0.28);
  }
  .cover--charcoal { left: 72px; background: var(--cover-charcoal); }
  .cover--midnight { left: 622px; background: var(--cover-midnight); }
  .cover__tab {
    position: absolute;
    top: 71px;
    width: 44px;
    height: 44px;
    background: var(--tab-slate);
  }
  .cover__tab--left { left: 0; }
  .cover__tab--right { right: 0; }
  .cover__title {
    position: absolute;
    top: 73px;
    left: 0; right: 0;
    margin: 0;
    text-align: center;
    color: var(--title-orange);
    font-size: 33px;
    font-weight: 700;
    line-height: 42px;
  }
  .cover__subtitle {
    position: absolute;
    left: 0; right: 0;
    margin: 0;
    text-align: center;
    color: var(--subtitle-white);
  }
  .cover--charcoal .cover__subtitle {
    top: 130px;
    font-size: 22px;
    font-weight: 700;
    line-height: 36px;
    letter-spacing: 0.01em;
  }
  .cover--midnight .cover__subtitle {
    top: 132px;
    font-size: 17.5px;
    font-weight: 400;
    line-height: 36px;
    letter-spacing: 0.08em;
    text-transform: uppercase;
  }
  .cover__art {
    position: absolute;
    top: 223px;
    left: 88px;
    width: 302px;
    height: 418px;
  }
  .cover--charcoal .cover__art {
    background: linear-gradient(180deg, var(--art-green) 0%, var(--art-teal) 38%, var(--art-plum) 72%, var(--art-green) 100%);
  }
  .cover--midnight .cover__art {
    background: linear-gradient(180deg, var(--art-green) 0%, var(--art-blue) 38%, var(--art-rose) 72%, var(--art-green) 100%);
  }
  .cover__author {
    position: absolute;
    top: 652px;
    left: 0; right: 0;
    margin: 0;
    text-align: center;
    color: var(--title-orange);
    font-size: 23px;
    line-height: 32px;
  }
  .cover--charcoal .cover__author { font-weight: 400; }
  .cover--midnight .cover__author { font-weight: 700; }
</style>
</head>
<body>
<main class="canvas">

  <article class="cover cover--charcoal">
    <div class="cover__tab cover__tab--left"></div>
    <div class="cover__tab cover__tab--right"></div>
    <h1 class="cover__title">The 4Cs Approach</h1>
    <p class="cover__subtitle">Practical Bargaining and Persuasion<br>Methods for Cross-Cultural Success</p>
    <div class="cover__art" role="img" aria-label="Cover illustration: a globe behind overlapping translucent coloured panels in cool blue, teal and violet tones"></div>
    <p class="cover__author">Ravindra K. Malhotra</p>
  </article>

  <article class="cover cover--midnight">
    <div class="cover__tab cover__tab--left"></div>
    <div class="cover__tab cover__tab--right"></div>
    <h1 class="cover__title">The 4Cs Approach</h1>
    <p class="cover__subtitle">Practical Bargaining and Persuasion<br>Methods for Cross-Cultural Success</p>
    <div class="cover__art" role="img" aria-label="Cover illustration: a globe behind overlapping translucent coloured panels in warm rose, blue and green tones"></div>
    <p class="cover__author">Ravindra K. Malhotra</p>
  </article>

</main>
</body>
</html>
```